Stylish Business Cards Wanted

- DOUBLE SIDED Design Required -

High end, edgy cards for a corporate and personal stylist. Must include logo,
Name: Belinda Harwick
Title: Director and Stylist
telephone : +61 8 7142 5809
email: belinda@theloombriefing.example
website: theloombriefing.example
Tag: Corporate Workwear & Uniform Specialist | Personal Stylist
Would like nice icons for telephone, email, website

Target Market(s)

Businesses wanting stylish uniforms, people wanting stylish wardrobes

Industry/Entity Type

Corporate Workwear Stylist

Contact Information for Business Card

I would like black, white and gold foiling incorporated in the design - possibly a touch of the other colours on my branding guide attached Name: Belinda Harwick Title: Director and Stylist telephone : +61 8 7142 5809 email: belinda@theloombriefing.example website: theloombriefing.example Tag: Corporate Workwear & Uniform Specialist | Personal Stylist Would like nice icons for telephone, email, website

Font styles to use
Other font styles liked:
• Raleway

Colors

Designer to choose colors to be used in the design.

Requirements
Must have
• Gold foil accents

```html
<!DOCTYPE html>
<html lang="en">
<head>
<meta charset="utf-8">
<title>The Loom Briefing – Business Cards</title>
<link rel="stylesheet" href="https://fonts.googleapis.com/css2?family=Montserrat:wght@400;500;700&display=swap">
<style>
  :root {
    --backdrop: #2b2b2b;
    --card-dark: #1f1f1f;
    --card-light: #3a3a3a;
    --gold: #e8c15a;
    --white: #ffffff;
    --ghost: rgba(255, 255, 255, 0.05);
  }
  * { margin: 0; padding: 0; box-sizing: border-box; }
  html, body {
    width: 1200px; height: 900px; overflow: hidden;
    background: var(--backdrop);
    font-family: "Montserrat", sans-serif;
  }
  .sheet {
    width: 1200px; height: 900px;
    display: flex; flex-direction: column; align-items: center; justify-content: center;
    gap: 40px;
  }
  .card {
    position: relative;
    width: 700px; height: 400px;
    background: linear-gradient(115deg, var(--card-dark) 35%, var(--card-light) 100%);
    box-shadow: 0 10px 24px rgba(0, 0, 0, 0.5);
    overflow: hidden;
  }
  .card__foil-band {
    position: absolute; left: 0; right: 0; bottom: 0;
    height: 12px; background: var(--gold);
  }
  .brand-name {
    color: var(--white);
    font-weight: 700;
    letter-spacing: 0.06em;
    text-transform: uppercase;
    white-space: nowrap;
    display: flex; align-items: center; gap: 12px;
  }
  .brand-name__dot {
    width: 14px; height: 14px; border-radius: 50%; background: var(--gold); flex: none;
  }
  /* Front */
  .card--front .brand-name {
    position: absolute; top: 120px; left: 0; right: 0; justify-content: center;
    font-size: 40px; padding-left: 140px;
  }
  .tagline {
    position: absolute; left: 40px; right: 40px; bottom: 46px;
    color: var(--gold); font-size: 14px; font-weight: 500;
    letter-spacing: 0.06em; text-transform: uppercase; text-align: right;
    white-space: nowrap;
  }
  /* Back */
  .card--back .brand-name {
    position: absolute; top: 56px; left: 50px; font-size: 24px;
  }
  .card--back .brand-name__dot { width: 12px; height: 12px; }
  .holder {
    position: absolute; top: 120px; right: 34px; text-align: right;
    padding-right: 22px;
  }
  .holder__name {
    color: var(--gold); font-size: 24px; font-weight: 700; letter-spacing: 0.05em;
    text-transform: uppercase; white-space: nowrap;
  }
  .holder__title { color: var(--white); font-size: 16px; font-weight: 500; margin-top: 4px; letter-spacing: 0.03em; }
  .holder__marker {
    position: absolute; right: 0; top: 34px; width: 8px; height: 40px; background: var(--gold);
  }
  .ghost-mark {
    position: absolute; right: 36px; bottom: 40px;
    color: var(--ghost); font-size: 88px; font-weight: 700; text-transform: uppercase;
    letter-spacing: 0.04em; white-space: nowrap;
  }
  .contacts {
    position: absolute; left: 50px; bottom: 46px; list-style: none;
    color: var(--white); font-size: 18px; font-weight: 500;
  }
  .contacts__item { display: flex; align-items: center; gap: 12px; margin-top: 8px; white-space: nowrap; }
  .contacts__icon { width: 20px; height: 20px; flex: none; }
</style>
</head>
<body>
<main class="sheet">
  <section class="card card--front" aria-label="Business card front">
    <div class="brand-name"><span class="brand-name__dot"></span>The Loom Briefing</div>
    <p class="tagline">Corporate Workwear | Uniform Specialist | Personal Stylist</p>
    <div class="card__foil-band"></div>
  </section>

  <section class="card card--back" aria-label="Business card back">
    <div class="ghost-mark" aria-hidden="true">Loom</div>
    <div class="brand-name"><span class="brand-name__dot"></span>The Loom Briefing</div>
    <div class="holder">
      <div class="holder__name">Belinda Harwick</div>
      <div class="holder__title">Director and Stylist</div>
      <span class="holder__marker"></span>
    </div>
    <ul class="contacts">
      <li class="contacts__item">
        <svg class="contacts__icon" viewBox="0 0 24 24"><path fill="#e8c15a" d="M6.6 10.8a15.1 15.1 0 0 0 6.6 6.6l2.2-2.2a1 1 0 0 1 1-.25 11.4 11.4 0 0 0 3.6.57 1 1 0 0 1 1 1V20a1 1 0 0 1-1 1A17 17 0 0 1 3 4a1 1 0 0 1 1-1h3.5a1 1 0 0 1 1 1c0 1.25.2 2.45.57 3.6a1 1 0 0 1-.25 1z"/></svg>
        +61 8 7142 5809
      </li>
      <li class="contacts__item">
        <svg class="contacts__icon" viewBox="0 0 24 24"><rect x="2" y="5" width="20" height="14" fill="#e8c15a"/><path d="M2 5l10 8 10-8" fill="none" stroke="#1f1f1f" stroke-width="1.6"/></svg>
        belinda@theloombriefing.example
      </li>
      <li class="contacts__item">
        <svg class="contacts__icon" viewBox="0 0 24 24"><circle cx="12" cy="12" r="9.5" fill="none" stroke="#e8c15a" stroke-width="2"/><ellipse cx="12" cy="12" rx="4" ry="9.5" fill="none" stroke="#e8c15a" stroke-width="1.6"/><path d="M2.5 12h19" stroke="#e8c15a" stroke-width="1.6"/></svg>
        www.theloombriefing.example
      </li>
    </ul>
    <div class="card__foil-band"></div>
  </section>
</main>
</body>
</html>
```